Design NEW business card

We would like a business card using the colour deep red wine or dark navy blue textured background (patterned or not, open to suggestions) with a high gloss debossed rose gold/copper Roland Mercer Jewellery business name (Provided). I have included images for your review we would like to keep our currently logo and business name on the front but you can change the layout and positioning. For the back of the card we are open to all suggestions/variations.
Business
Use our current Roland Mercer Jewellery logo (Provided image)

```html
<!DOCTYPE html>
<html lang="en">
<head>
<meta charset="utf-8">
<title>Roland Mercer Jewellery – Business Card</title>
<link rel="stylesheet" href="https://fonts.googleapis.com/css2?family=Open+Sans:wght@400;600;700&display=swap">
<style>
  :root {
    --page-bg: #ecebe8;
    --card-white: #fbfaf8;
    --copper: #c08f72;
    --copper-text: #b98163;
    --ink: #1d1d1d;
    --wine: #5a1e24;
    --wine-deep: #4a161b;
    --deboss: #3f1216;
    --card-shadow: rgba(40, 20, 15, 0.18);
  }
  * { margin: 0; padding: 0; box-sizing: border-box; }
  html, body {
    width: 1200px;
    height: 900px;
    overflow: hidden;
    background: var(--page-bg);
    font-family: "Open Sans", Arial, sans-serif;
  }
  .sheet {
    width: 1200px;
    height: 900px;
    display: flex;
    flex-direction: column;
    align-items: center;
    justify-content: center;
    gap: 40px;
  }
  .card {
    position: relative;
    width: 680px;
    height: 388px;
    box-shadow: 0 6px 18px var(--card-shadow);
    overflow: hidden;
  }

  /* Front */
  .card-front { background: var(--card-white); }
  .card-front .shapes {
    position: absolute;
    inset: 0;
  }
  .holder {
    position: absolute;
    left: 108px;
    top: 24px;
  }
  .holder-name {
    font-size: 25px;
    font-weight: 700;
    color: var(--copper-text);
    line-height: 1.1;
  }
  .holder-role {
    font-size: 16px;
    color: var(--ink);
    margin-top: 2px;
  }
  .contact {
    position: absolute;
    left: 34px;
    top: 150px;
    font-size: 18px;
    color: var(--ink);
    line-height: 1.28;
  }
  .contact-address { margin-bottom: 4px; }
  .contact-line {
    display: flex;
    align-items: center;
    gap: 12px;
  }
  .contact-line svg { width: 13px; height: 13px; flex: none; }
  .brand {
    position: absolute;
    left: 400px;
    top: 160px;
    display: flex;
    align-items: center;
    gap: 12px;
  }
  .brand-dot {
    width: 12px;
    height: 12px;
    border-radius: 50%;
    background: var(--copper);
  }
  .brand-name {
    font-size: 19px;
    font-weight: 400;
    letter-spacing: 0.22em;
    text-transform: uppercase;
    color: var(--copper-text);
    line-height: 1.5;
  }

  /* Back */
  .card-back {
    background: radial-gradient(ellipse at 50% 45%, var(--wine) 0%, var(--wine-deep) 100%);
    display: flex;
    align-items: center;
    justify-content: center;
  }
  .back-name {
    font-size: 26px;
    font-weight: 400;
    letter-spacing: 0.24em;
    text-transform: uppercase;
    color: var(--deboss);
  }
</style>
</head>
<body>
<main class="sheet">

  <section class="card card-front" aria-label="Business card front">
    <svg class="shapes" width="680" height="388" viewBox="0 0 680 388" aria-hidden="true">
      <polygon points="0,0 92,0 70,44 0,44" fill="var(--copper)"/>
      <polygon points="0,324 300,324 292,340 0,340" fill="var(--copper)"/>
      <polygon points="0,346 289,346 275,376 0,376" fill="var(--copper)"/>
      <polygon points="306,324 680,324 680,388 0,388 0,382 280,382" fill="var(--copper)"/>
    </svg>

    <div class="holder">
      <p class="holder-name">Daniel Hartley</p>
      <p class="holder-role">Managing Director</p>
    </div>

    <div class="contact">
      <p class="contact-address">48 Harbour Lane, Westfield<br>Northbrook, 204871.</p>
      <p class="contact-line">
        <svg viewBox="0 0 16 16" aria-hidden="true"><path d="M4 1l3 3-2 2c1 2 3 4 5 5l2-2 3 3-2 2C7 14 2 9 2 3z" fill="var(--copper)"/></svg>
        021-487 903 516
      </p>
      <p class="contact-line">
        <svg viewBox="0 0 16 16" aria-hidden="true"><rect x="1" y="3" width="14" height="10" fill="var(--copper)"/><path d="M1 3l7 6 7-6" fill="none" stroke="var(--card-white)" stroke-width="1.4"/></svg>
        hello@rmercer.net
      </p>
      <p class="contact-line">
        <svg viewBox="0 0 16 16" aria-hidden="true"><path d="M6 10l4-4M7 4l2-2a3 3 0 014 4l-2 2M9 12l-2 2a3 3 0 01-4-4l2-2" fill="none" stroke="var(--copper)" stroke-width="1.8" stroke-linecap="round"/></svg>
        www.rmercerjewels.com
      </p>
    </div>

    <div class="brand">
      <span class="brand-dot"></span>
      <p class="brand-name">Roland Mercer<br>Jewellery</p>
    </div>
  </section>

  <section class="card card-back" aria-label="Business card back">
    <p class="back-name">Roland Mercer Jewellery</p>
  </section>

</main>
</body>
</html>
```